Budget Brand Responsive Website

Flat vector style website needed for value based IT support company. looking for clean, illustration intensive based design. Current test site can be found at www.bright-mend.co.uk and holding page it www.brightmend.co.uk this will show text and services, please feel free to use placeholder text if you think we need alternative text in places. Emphasis should be on low cost support and services listed on the site, would be nice to see costs in bold images. important colors are the blue, orange and white, see holding page and attached image of an advert

It Company

```html
<!DOCTYPE html>
<html lang="en">
<head>
<meta charset="utf-8">
<title>Bright Mend – IT Support</title>
<link href="https://fonts.googleapis.com/css2?family=Open+Sans:wght@400;600;700;800&display=swap" rel="stylesheet">
<style>
:root{
  --blue:#2e6fb8;
  --blue-dark:#1d4f8c;
  --blue-light:#4d8fd6;
  --orange:#ea7a1e;
  --orange-dark:#c9610f;
  --ink:#333a40;
  --muted:#8a9096;
  --grey-bg:#eef0f2;
  --line:#dde1e5;
  --footer:#3a3d40;
  --footer-deep:#2b2d30;
  --white:#ffffff;
}
*{box-sizing:border-box;margin:0;padding:0}
html,body{width:1200px;height:2528px;overflow:hidden}
body{font-family:"Open Sans",Arial,sans-serif;color:var(--ink);background:var(--white);font-size:14px;line-height:1.55}
.wrap{width:940px;margin:0 auto;position:relative}
.btn{display:inline-block;background:var(--orange);color:var(--white);font-size:14px;font-weight:600;padding:12px 26px;border-radius:2px}

/* header */
.site-header{height:112px;background:var(--white);border-bottom:1px solid var(--line)}
.site-header .wrap{height:112px;display:flex;align-items:center;justify-content:space-between}
.brand{font-size:26px;font-weight:600;color:var(--ink);line-height:1}
.header-right{text-align:right}
.phone{font-size:15px;font-weight:600;color:var(--ink);display:flex;align-items:center;gap:8px;justify-content:flex-end;margin-bottom:14px}
.nav{display:flex;gap:40px;font-size:13px;font-weight:600;text-transform:uppercase;color:var(--ink)}
.nav .active{color:var(--orange);border-bottom:3px solid var(--orange);padding-bottom:4px}

/* hero */
.hero{height:496px;position:relative;background:radial-gradient(ellipse at 72% 55%,#3f78b4 0%,#1c3e66 40%,#0d1d33 80%);color:var(--white)}
.hero .wrap{padding-top:78px}
.hero-kicker{font-size:20px;font-weight:400;letter-spacing:.5px}
.hero-title{font-size:38px;font-weight:700;margin:4px 0 14px}
.hero-text{width:420px;font-size:14px;color:#d5e1ee;margin-bottom:26px}
.hero-arrow{position:absolute;top:228px;width:34px;height:34px;border-radius:50%;background:rgba(255,255,255,.25);display:flex;align-items:center;justify-content:center}
.hero-arrow.left{left:24px}.hero-arrow.right{right:24px}

/* services */
.services{height:452px;background:var(--grey-bg);padding-top:86px}
.section-title{text-align:center;font-size:28px;font-weight:700;color:var(--ink);letter-spacing:.5px}
.section-rule{width:60px;height:3px;background:var(--orange);margin:12px auto 40px}
.service-row{display:flex;justify-content:space-between;padding:0 22px}
.service{width:200px;text-align:center}
.service-icon{width:92px;height:92px;border-radius:50%;background:var(--blue);margin:0 auto 16px;display:flex;align-items:center;justify-content:center;box-shadow:0 0 0 6px #d7e3f1}
.service h3{font-size:15px;font-weight:700;text-transform:uppercase;margin-bottom:6px}
.service p{font-size:12px;color:var(--muted);line-height:1.5}

/* pricing */
.pricing{height:500px;padding-top:70px}
.price-row{display:flex;justify-content:space-between}
.plan{width:220px;border:1px solid var(--line);background:var(--white);box-shadow:0 2px 6px rgba(0,0,0,.08);position:relative;height:250px}
.plan-head{background:linear-gradient(var(--blue-light),var(--blue));color:var(--white);text-align:center;padding:14px 8px 12px;height:84px}
.plan-head h3{font-size:21px;font-weight:700;line-height:1.1}
.plan-head p{font-size:13px;font-weight:600;line-height:1.25;margin-top:4px}
.plan ul{list-style:none;padding:14px 20px}
.plan li{font-size:12px;color:var(--muted);padding:6px 0;border-bottom:1px solid #eef0f2;display:flex;align-items:center;gap:8px}
.plan-more{position:absolute;left:-8px;right:-8px;bottom:-18px;height:38px;background:var(--orange);color:var(--white);font-weight:700;font-size:15px;text-align:center;line-height:38px}

/* expectations */
.expect{height:320px;background:linear-gradient(100deg,#0f2035 0%,#1f3d5f 55%,#2f5a86 100%);color:var(--white)}
.expect .wrap{display:flex;align-items:center;height:320px;gap:50px}
.expect h2{font-size:30px;font-weight:700;margin-bottom:10px}
.expect p{font-size:13px;color:#cdd8e4;width:560px;margin-bottom:18px}
.expect .btn{background:transparent;border:1px solid #cdd8e4;padding:8px 20px;font-size:12px}

/* about */
.about{height:340px}
.about .wrap{display:flex;align-items:center;height:340px;gap:50px}
.about-photo{width:300px;height:210px;flex:none;background:linear-gradient(135deg,#e6ebf0,#b7c6d6 60%,#8aa2bb)}
.about h2{font-size:30px;font-weight:700;margin-bottom:6px}
.about .section-rule{margin:0 0 16px}
.about p{font-size:12px;color:var(--muted);margin-bottom:20px}

/* footer */
.site-footer{height:268px;background:var(--footer);color:#c2c6ca;padding-top:36px}
.footer-cols{display:flex;justify-content:space-between}
.footer-col{width:210px}
.footer-col h4{color:var(--white);font-size:15px;font-weight:700;text-transform:uppercase;margin-bottom:14px}
.footer-col p,.footer-col li{font-size:12px;line-height:1.6}
.footer-col ul{list-style:none}
.footer-col li{display:flex;align-items:center;gap:8px;margin-bottom:4px}
.blog-item{display:flex;gap:10px;margin-bottom:12px}
.blog-thumb{width:44px;height:36px;flex:none;background:linear-gradient(135deg,#6f8aa6,#3e5670)}
.blog-item p{font-size:11px;line-height:1.45}
.contact-line{display:flex;gap:10px;align-items:flex-start;margin-bottom:12px;font-size:12px}
.bottom-bar{height:40px;background:var(--footer-deep);color:#9aa0a6;font-size:11px}
.bottom-bar .wrap{display:flex;justify-content:space-between;align-items:center;height:40px}
.social{display:flex;gap:8px}
.social span{width:20px;height:20px;border-radius:50%;border:1px solid #8a9096}
</style>
</head>
<body>

<header class="site-header">
  <div class="wrap">
    <div class="brand">Bright Mend</div>
    <div class="header-right">
      <div class="phone">
        <svg width="16" height="16" viewBox="0 0 24 24"><path d="M6.6 10.8a15 15 0 0 0 6.6 6.6l2.2-2.2a1 1 0 0 1 1-.25 11.4 11.4 0 0 0 3.6.57 1 1 0 0 1 1 1V20a1 1 0 0 1-1 1A17 17 0 0 1 3 4a1 1 0 0 1 1-1h3.5a1 1 0 0 1 1 1c0 1.25.2 2.45.57 3.57a1 1 0 0 1-.25 1z" fill="#2e6fb8"/></svg>
        01632 960 418
      </div>
      <nav class="nav">
        <span class="active">Home</span><span>Support</span><span>Services</span><span>About</span><span>Contact</span>
      </nav>
    </div>
  </div>
</header>

<section class="hero" role="img" aria-label="Hand touching a glowing network of connected devices over a dark blue city background">
  <div class="hero-arrow left"><svg width="12" height="12" viewBox="0 0 12 12"><path d="M8 1 3 6l5 5" stroke="#fff" stroke-width="2" fill="none"/></svg></div>
  <div class="hero-arrow right"><svg width="12" height="12" viewBox="0 0 12 12"><path d="M4 1l5 5-5 5" stroke="#fff" stroke-width="2" fill="none"/></svg></div>
  <div class="wrap">
    <div class="hero-kicker">DELIVERING SOLUTIONS TO MAXIMISE UPTIME</div>
    <h1 class="hero-title">MINIMISE DISRUPTION</h1>
    <p class="hero-text">Lorem Ipsum is simply dummy text of the printing and typesetting industry. Lorem Ipsum has been the industry's standard dummy text ever since Lorem Ipsum is simply dummy.</p>
    <span class="btn">Show the Details</span>
  </div>
</section>

<section class="services">
  <h2 class="section-title">OUR SERVICES</h2>
  <div class="section-rule"></div>
  <div class="wrap service-row">
    <div class="service">
      <div class="service-icon"><svg width="40" height="40" viewBox="0 0 40 40" fill="none" stroke="#fff" stroke-width="3"><path d="M8 22v-4a12 12 0 0 1 24 0v4"/><rect x="5" y="21" width="7" height="10" rx="2" fill="#fff"/><rect x="28" y="21" width="7" height="10" rx="2" fill="#fff"/></svg></div>
      <h3>Support</h3>
      <p>Benefit from our additional support at reduced rates, keeping you working through every issue.</p>
    </div>
    <div class="service">
      <div class="service-icon"><svg width="38" height="38" viewBox="0 0 24 24"><path d="M6.6 10.8a15 15 0 0 0 6.6 6.6l2.2-2.2a1 1 0 0 1 1-.25 11.4 11.4 0 0 0 3.6.57 1 1 0 0 1 1 1V20a1 1 0 0 1-1 1A17 17 0 0 1 3 4a1 1 0 0 1 1-1h3.5a1 1 0 0 1 1 1c0 1.25.2 2.45.57 3.57a1 1 0 0 1-.25 1z" fill="#fff"/></svg></div>
      <h3>Voice</h3>
      <p>Benefit from lower call charges and flexible lines that grow with your business needs.</p>
    </div>
    <div class="service">
      <div class="service-icon"><svg width="40" height="40" viewBox="0 0 40 40"><rect x="5" y="7" width="30" height="20" rx="2" fill="none" stroke="#fff" stroke-width="3"/><path d="M15 33h10M20 27v6" stroke="#fff" stroke-width="3"/></svg></div>
      <h3>Internet</h3>
      <p>Benefit from fast reliable connections with monitoring so your team stays online all day.</p>
    </div>
    <div class="service">
      <div class="service-icon"><svg width="36" height="40" viewBox="0 0 36 40"><path d="M18 3 4 9v10c0 9 6 15 14 18 8-3 14-9 14-18V9z" fill="none" stroke="#fff" stroke-width="3"/><path d="M12 20l4 4 8-8" stroke="#fff" stroke-width="3" fill="none"/></svg></div>
      <h3>Security</h3>
      <p>Benefit from antivirus, backup and firewall care that protects your data every single day.</p>
    </div>
  </div>
</section>

<section class="pricing">
  <h2 class="section-title">PRICING FOR POPULAR SERVICES</h2>
  <div class="section-rule"></div>
  <div class="wrap price-row">
    <div class="plan">
      <div class="plan-head"><h3>Support</h3><p>Unlimited Monthly<br>Remote Support</p></div>
      <ul><li>&#10003; Per device £9.99 pm</li><li>&#10003; Per user £14.99 pm</li><li>&#10003; Onsite £45.00 per hour</li></ul>
      <div class="plan-more">More</div>
    </div>
    <div class="plan">
      <div class="plan-head"><h3>Voice</h3><p>Lower rates and<br>call charges</p></div>
      <ul><li>&#10003; SIM from £6.00 pm</li><li>&#10003; Line rental from £9.50</li><li>&#10003; Phones from £24.00</li></ul>
      <div class="plan-more">More</div>
    </div>
    <div class="plan">
      <div class="plan-head"><h3>Hosting</h3><p>Flexible and Secure</p></div>
      <ul><li>&#10003; Email hosting from £2.50</li><li>&#10003; Web hosting from £5.00</li><li>&#10003; Office from £7.99 pm</li></ul>
      <div class="plan-more">More</div>
    </div>
    <div class="plan">
      <div class="plan-head"><h3>Cloud</h3><p>Reduce costs &amp; increase<br>Performance</p></div>
      <ul><li>&#10003; Online backup</li><li>&#10003; Private cloud servers</li><li>&#10003; Virtual desktops</li></ul>
      <div class="plan-more">More</div>
    </div>
  </div>
</section>

<section class="expect" role="img" aria-label="Dark blue background of a person working at a computer">
  <div class="wrap">
    <svg width="150" height="150" viewBox="0 0 150 150">
      <circle cx="75" cy="75" r="62" fill="none" stroke="rgba(255,255,255,.2)" stroke-width="12"/>
      <circle cx="75" cy="75" r="62" fill="none" stroke="#fff" stroke-width="12" stroke-dasharray="370 390" transform="rotate(-90 75 75)"/>
      <text x="75" y="86" text-anchor="middle" font-family="Open Sans, sans-serif" font-size="32" font-weight="700" fill="#fff">95%</text>
    </svg>
    <div>
      <h2>WE EXCEED EXPECTATIONS</h2>
      <p>Lorem ipsum dolor sit amet, consectetur adipiscing elit. Our team works hard to keep every system running and every customer happy. We measure our service against clear targets and report back each month, so you always know how your support is performing. Most of our clients rate us above their expectations.</p>
      <span class="btn">Read More</span>
    </div>
  </div>
</section>

<section class="about">
  <div class="wrap">
    <div class="about-photo" role="img" aria-label="Hands typing on a laptop keyboard on a white desk"></div>
    <div>
      <h2>ABOUT BRIGHT MEND</h2>
      <div class="section-rule"></div>
      <p>Our IT is a trusted leading Managed Service Provider offering value based support to small and medium businesses. With years of industry experience, our commitment to delivering tailored technology solutions has made us a reliable partner for local companies. We continue to grow through referrals, clear pricing and a friendly team that cares about keeping you productive. From help desk to cloud services, we manage your IT so that you can focus on running your business.</p>
      <span class="btn">Read more info</span>
    </div>
  </div>
</section>

<footer class="site-footer">
  <div class="wrap footer-cols">
    <div class="footer-col">
      <h4>About Us</h4>
      <p>Lorem ipsum is simply dummy text of the printing and typesetting industry. Lorem ipsum has been the industry standard dummy text ever since.</p>
    </div>
    <div class="footer-col">
      <h4>Quick Links</h4>
      <ul><li>&#8250; Home</li><li>&#8250; Support</li><li>&#8250; Services</li><li>&#8250; About</li><li>&#8250; Contact</li></ul>
    </div>
    <div class="footer-col">
      <h4>Our Latest Blog</h4>
      <div class="blog-item"><div class="blog-thumb" role="img" aria-label="Blog thumbnail"></div><p>Lorem ipsum dummy text here<br>November 21, 2014<br>10 Comments</p></div>
      <div class="blog-item"><div class="blog-thumb" role="img" aria-label="Blog thumbnail"></div><p>Lorem ipsum dummy text here<br>November 21, 2014<br>10 Comments</p></div>
    </div>
    <div class="footer-col">
      <h4>Contact Details</h4>
      <div class="contact-line"><svg width="14" height="18" viewBox="0 0 14 18"><path d="M7 0a7 7 0 0 0-7 7c0 5 7 11 7 11s7-6 7-11a7 7 0 0 0-7-7zm0 9.5A2.5 2.5 0 1 1 7 4.5a2.5 2.5 0 0 1 0 5z" fill="#ea7a1e"/></svg><span>12 Harbour Row, Unit 4,<br>Westbridge, WB1 2AA</span></div>
      <div class="contact-line"><svg width="14" height="14" viewBox="0 0 24 24"><path d="M6.6 10.8a15 15 0 0 0 6.6 6.6l2.2-2.2a1 1 0 0 1 1-.25 11.4 11.4 0 0 0 3.6.57 1 1 0 0 1 1 1V20a1 1 0 0 1-1 1A17 17 0 0 1 3 4a1 1 0 0 1 1-1h3.5a1 1 0 0 1 1 1c0 1.25.2 2.45.57 3.57a1 1 0 0 1-.25 1z" fill="#ea7a1e"/></svg><span>01632 960 418</span></div>
      <div class="contact-line"><svg width="16" height="12" viewBox="0 0 16 12"><rect width="16" height="12" rx="1" fill="#ea7a1e"/><path d="M0 1l8 6 8-6" stroke="#3a3d40" stroke-width="1.5" fill="none"/></svg><span>hello@bright-mend.co.uk</span></div>
    </div>
  </div>
</footer>
<div class="bottom-bar">
  <div class="wrap">
    <span>Copyright 2014 Bright Mend. All Rights Reserved</span>
    <div class="social"><span></span><span></span><span></span><span></span></div>
  </div>
</div>

</body>
</html>
```